Website for new dental office

I am Dr. Colin Ashford and am building a new dental practice. I specialize in general dentistry. I am young and have a higher end dental practice incorporating very new technologies and would like my website to reflect that. As many dental patients are older, the website must be very easy to navigate. I would like patients to be able to request appointments, and will eventually add on patient information forms (the health history, etc, that you normally fill out in the practice) from my practice management software, so leave an area for that.

Industry/Entity Type

Building

```html
<!DOCTYPE html>
<html lang="en">
<head>
<meta charset="utf-8">
<title>Colin Ashford, DDS – General Dentistry</title>
<link href="https://fonts.googleapis.com/css2?family=Open+Sans:wght@300;400;600;700&family=Roboto:wght@300;400;500;700&display=swap" rel="stylesheet">
<style>
:root{
  --blue:#1a8ad8;
  --navy:#14487f;
  --nav-top:#2f86d3;
  --nav-bottom:#1c64ad;
  --nav-active:#0f3f7a;
  --green-top:#9ad532;
  --green-bottom:#6fb016;
  --orange-top:#ffa53a;
  --orange-bottom:#f27a0c;
  --text:#4a4a4a;
  --muted:#8a8a8a;
  --line:#dedede;
  --band:#dcedf5;
}
*{margin:0;padding:0;box-sizing:border-box}
html,body{width:958px;height:1200px;overflow:hidden;background:#fff}
body{position:relative;font-family:"Open Sans",sans-serif;color:var(--text)}
.abs{position:absolute}
.header-bg{left:0;top:0;width:958px;height:110px;background:linear-gradient(#bcdcf8,#ffffff)}
.brand{left:84px;top:38px;font-family:"Open Sans",sans-serif;font-weight:600;font-size:26px;color:#2a72c6;letter-spacing:.3px}
.cta-top{left:654px;top:13px;width:216px;height:33px;border-radius:2px;background:linear-gradient(var(--green-top),var(--green-bottom));color:#1c2a05;font:700 12px "Open Sans",sans-serif;display:flex;align-items:center;justify-content:center;gap:8px}
.phone{left:700px;top:58px;width:168px;text-align:right;font:400 18px "Roboto",sans-serif;color:#222;display:flex;justify-content:flex-end;align-items:center;gap:6px}
.nav{left:88px;top:100px;width:782px;height:30px;background:linear-gradient(var(--nav-top),var(--nav-bottom));border-radius:2px}
.nav a{position:absolute;top:0;height:30px;line-height:30px;color:#fff;text-decoration:none;font:400 11.5px "Roboto",sans-serif;transform:translateX(-50%);white-space:nowrap}
.nav a.active{left:0;transform:none;width:61px;text-align:center;background:var(--nav-active);font-weight:700}
.hero{left:88px;top:138px;width:782px;height:284px;border:1px solid #d8dde2;border-radius:3px;overflow:hidden;background:linear-gradient(100deg,#e9edf0 0%,#f3f5f6 40%,#e6ebef 62%,#dfe4e8 100%)}
.hero-photo{position:absolute;left:430px;top:0;width:352px;height:284px;background:radial-gradient(ellipse at 45% 40%,#f4f6f8 0%,#e2e7eb 55%,#d6dde3 100%)}
.hero h1{position:absolute;left:26px;top:92px;font:300 27px "Open Sans",sans-serif;color:#1f74c4;letter-spacing:-.5px}
.hero h1 strong{font-weight:700;color:var(--navy)}
.hero p{position:absolute;left:26px;top:128px;font:500 13.5px "Roboto",sans-serif;color:var(--navy)}
.hero-btn{position:absolute;left:27px;top:156px;width:199px;height:37px;border-radius:3px;background:linear-gradient(#6cc11e,#3f9a0f);border:1px solid #3b8d0b;color:#fff;font:400 18px "Roboto",sans-serif;display:flex;align-items:center;justify-content:center;gap:5px}
.hero-btn b{font-weight:700}
.appt{left:88px;top:433px;width:782px;height:66px;background:linear-gradient(90deg,#f0f7fa,var(--band) 60%,#cfe6f0);border-left:8px solid #2b2b2b}
.appt-label{left:105px;top:458px;font:500 14px "Roboto",sans-serif;color:#1c1c1c}
.field{height:22px;background:#f7f8f8;border:1px solid #d3d6d8;font:400 8.5px "Roboto",sans-serif;color:#8a8a8a;padding-left:10px;line-height:20px}
.appt-btn{left:656px;top:469px;width:188px;height:26px;border-radius:3px;background:linear-gradient(var(--orange-top),var(--orange-bottom));color:#fff;font:700 12px "Roboto",sans-serif;display:flex;align-items:center;justify-content:center;gap:6px}
.tab{top:526px;height:33px;border:1px solid var(--line);border-bottom:none;background:#f8f8f8;font:400 12.5px "Roboto",sans-serif;color:#999;display:flex;align-items:center;justify-content:center}
.tab.active{background:#fff;color:var(--blue);border-top:3px solid var(--blue);height:34px;z-index:2}
.panel{left:88px;top:558px;width:782px;height:230px;border:1px solid var(--line);background:#fff}
.panel-photo{left:106px;top:583px;width:281px;height:173px;border:2px solid #eee;background:linear-gradient(120deg,#e6ddd6 0%,#d6c4b6 30%,#e7eef3 60%,#cfe3ee 100%)}
.welcome{left:402px;top:581px;font:300 20px "Open Sans",sans-serif;color:var(--blue)}
.welcome-text{left:404px;top:615px;width:450px;font:400 9.6px/15.2px "Open Sans",sans-serif;color:#444}
.btn-grey{left:402px;top:733px;width:96px;height:30px;background:#8e8e8e;color:#fff;font:400 11.5px "Roboto",sans-serif;display:flex;align-items:center;justify-content:center}
.lower{left:88px;top:808px;width:780px;height:354px;background:#fff;border:1px solid #eee;box-shadow:0 6px 18px rgba(0,0,0,.12)}
.section-title{font:400 20px "Open Sans",sans-serif;color:var(--blue)}
.rule{height:3px;background:var(--blue)}
.dots{height:0;border-top:1px dotted #bbb}
.case-img{top:878px;height:103px}
.case-title{top:986px;font:400 14.5px "Open Sans",sans-serif;color:var(--blue)}
.case-text{top:1021px;width:226px;font:400 9.6px/12.8px "Open Sans",sans-serif;color:#666}
.case-line{top:1106px;height:0;border-top:1px solid #ddd}
.read-more{top:1115px;font:italic 400 9px "Open Sans",sans-serif;color:#555;display:flex;align-items:center;gap:10px}
.read-more i{display:inline-block;width:11px;height:10px;background:#333;position:relative}
.read-more i::after{content:"";position:absolute;left:3px;top:2px;border-left:4px solid #fff;border-top:3px solid transparent;border-bottom:3px solid transparent}
.arrow-btn{top:842px;width:15px;height:14px;background:#eee;color:#bbb;font:400 10px "Roboto",sans-serif;text-align:center;line-height:14px}
.testimonial{left:598px;top:878px;width:239px;height:151px;border:1px solid #ddd;background:#fff}
.quote-text{left:614px;top:891px;width:210px;font:400 9.6px/14.4px "Open Sans",sans-serif;color:#666}
.quote-name{left:640px;top:951px;width:130px;text-align:right;font:700 12px "Roboto",sans-serif;color:#111}
.quote-mark{left:776px;top:930px;font:700 60px/1 "Open Sans",sans-serif;color:#eee}
.avatar-ring{left:614px;top:976px;width:80px;height:80px;border-radius:50%;background:#fff;border:1px solid #ddd;box-shadow:0 1px 4px rgba(0,0,0,.1)}
.avatar{left:622px;top:984px;width:64px;height:64px;border-radius:50%;background:radial-gradient(circle at 50% 45%,#6b4a38,#2a1d16)}
.schedule{left:599px;top:1078px;width:240px;height:65px;border-radius:2px;background:linear-gradient(var(--orange-top),var(--orange-bottom));color:#fff}
.schedule h3{position:absolute;left:9px;top:8px;font:400 15px "Open Sans",sans-serif}
.schedule p{position:absolute;left:10px;top:34px;width:180px;font:400 9.4px/12px "Open Sans",sans-serif}
.footer{left:0;top:1176px;width:976px;text-align:center;font:400 11px "Roboto",sans-serif;color:#222}
</style>
</head>
<body>

<div class="abs header-bg"></div>
<div class="abs brand">Colin Ashford, DDS</div>

<div class="abs cta-top">
  <svg width="15" height="13" viewBox="0 0 15 13" aria-hidden="true"><rect x="1" y="3" width="5" height="8" rx="1" fill="none" stroke="#1c2a05" stroke-width="1.5"/><rect x="9" y="3" width="5" height="8" rx="1" fill="none" stroke="#1c2a05" stroke-width="1.5"/><path d="M6 6h3" stroke="#1c2a05" stroke-width="1.5"/></svg>
  Request a FREE Consultation
</div>

<div class="abs phone">
  <svg width="24" height="22" viewBox="0 0 24 22" aria-hidden="true"><path d="M5 10c1 3 4 6 7 7l2-2c.5-.5 1-.5 1.5-.2l3 1.6c.5.3.6.9.3 1.3L17 20c-5 1-14-8-13-13l2.3-1.8c.4-.3 1-.2 1.3.3L9.2 8.5c.3.5.3 1-.2 1.5z" fill="#222"/><ellipse cx="10" cy="5" rx="6" ry="4" fill="none" stroke="#222" stroke-width="1.3"/><circle cx="8" cy="5" r=".9" fill="#222"/><circle cx="10" cy="5" r=".9" fill="#222"/><circle cx="12" cy="5" r=".9" fill="#222"/></svg>
  (123) 555-0148
</div>

<nav class="abs nav">
  <a class="active" href="#">HOME</a>
  <a href="#" style="left:114px">Our Team</a>
  <a href="#" style="left:211px">Philosophy</a>
  <a href="#" style="left:312px">Restorative</a>
  <a href="#" style="left:409px">Cosmetic</a>
  <a href="#" style="left:526px">Tooth Replacement</a>
  <a href="#" style="left:642px">First Visit</a>
  <a href="#" style="left:731px">Contact</a>
</nav>

<section class="abs hero">
  <div class="hero-photo" role="img" aria-label="Smiling young dentist in a white coat beside a modern dental chair"></div>
  <h1>I Specialize In <strong>General Dentistry</strong></h1>
  <p>Teeth Whitening Solutions for Everyone</p>
  <div class="hero-btn"><b>FREE</b> CONSULTANCY</div>
</section>

<div class="abs appt"></div>
<div class="abs appt-label">REQUEST AN APPOINTMENT</div>
<div class="abs field" style="left:288px;top:441px;width:178px">Your Name</div>
<div class="abs field" style="left:472px;top:441px;width:178px">Preferred date</div>
<div class="abs field" style="left:657px;top:441px;width:186px">Preferred day</div>
<div class="abs field" style="left:288px;top:471px;width:178px">Your Email</div>
<div class="abs field" style="left:472px;top:471px;width:178px">Phone number</div>
<div class="abs appt-btn">REQUEST AN APPOINTMENT
  <svg width="12" height="10" viewBox="0 0 12 10" aria-hidden="true"><path d="M1 1l4 4-4 4M6 1l4 4-4 4" fill="none" stroke="#fff" stroke-width="2"/></svg>
</div>

<div class="abs panel"></div>
<div class="abs tab active" style="left:102px;width:106px">Our Team</div>
<div class="abs tab" style="left:216px;width:104px">Patient Stories</div>
<div class="abs tab" style="left:329px;width:106px">health history</div>

<div class="abs panel-photo" role="img" aria-label="Dentist examining a smiling patient in the dental chair"></div>
<h2 class="abs welcome">Welcome to Colin Ashford, DDS</h2>
<p class="abs welcome-text">It is a long established fact that a reader will be distracted by the readable content of a page when looking at its layout. The point of using Lorem Ipsum is that it has a more-or-less normal distribution of letters, as opposed to using 'Content here, content here', making it look like readable English. Many desktop publishing packages and web page editors now use Lorem Ipsum as their default model text, and a search for 'lorem ipsum' will uncover many web sites still in their infancy. Various versions have evolved over the years, sometimes by accident, sometimes on purpose (injected humour and the like).</p>
<div class="abs btn-grey">READ MORE</div>

<section class="abs lower"></section>

<h2 class="abs section-title" style="left:98px;top:832px">Case Studies</h2>
<div class="abs rule" style="left:218px;top:848px;width:92px"></div>
<div class="abs dots" style="left:310px;top:849px;width:254px"></div>

<div class="abs case-img" style="left:105px;width:215px;background:linear-gradient(#f3ddd4,#c9242c 55%,#f1d7cd)" role="img" aria-label="Close-up of a bright white smile"></div>
<div class="abs case-img" style="left:342px;width:220px;background:linear-gradient(110deg,#e8d8cf,#d7a79c 50%,#f1ece9)" role="img" aria-label="Dental mirror examination of a patient's teeth"></div>

<h3 class="abs case-title" style="left:100px">Cosmetics</h3>
<div class="abs dots" style="left:100px;top:1008px;width:220px"></div>
<p class="abs case-text" style="left:100px">Lorem Ipsum is simply dummy text of the printing and typesetting industry. Lorem Ipsum has been the industry's standard dummy text ever since the 1500s,</p>
<div class="abs case-line" style="left:98px;width:222px"></div>
<div class="abs read-more" style="left:99px">Read more <i></i></div>

<h3 class="abs case-title" style="left:342px">Restorative</h3>
<div class="abs dots" style="left:342px;top:1008px;width:222px"></div>
<p class="abs case-text" style="left:345px">Lorem Ipsum is simply dummy text of the printing and typesetting industry. Lorem Ipsum has been the industry's standard dummy text ever since the 1500s,</p>
<div class="abs case-line" style="left:338px;width:221px"></div>
<div class="abs read-more" style="left:340px">Read more <i></i></div>

<h2 class="abs section-title" style="left:598px;top:837px;font-size:16px">Testimonials</h2>
<div class="abs rule" style="left:706px;top:848px;width:54px"></div>
<div class="abs dots" style="left:760px;top:849px;width:52px"></div>
<div class="abs arrow-btn" style="left:820px">‹</div>
<div class="abs arrow-btn" style="left:836px">›</div>

<div class="abs testimonial"></div>
<p class="abs quote-text">Lorem ipsum dolor slo onsec nelioro tue raliquet Morbi nec In Curabitur, lorem in design Morbi nec In Curabitur Ireaoreet nisl</p>
<div class="abs quote-mark">”</div>
<div class="abs quote-name">Daniel Hartley</div>
<div class="abs avatar-ring"></div>
<div class="abs avatar" role="img" aria-label="Portrait photo of the patient giving the testimonial"></div>

<div class="abs schedule">
  <h3>Schedule Your Appointment</h3>
  <p>Lorem Ipsum is simply dummy text of the printing and typesetting industry.</p>
  <svg style="position:absolute;left:193px;top:27px" width="32" height="30" viewBox="0 0 32 30" aria-hidden="true">
    <rect x="1.5" y="4" width="29" height="24.5" rx="2" fill="none" stroke="#3a2306" stroke-width="2"/>
    <path d="M1.5 10h29" stroke="#3a2306" stroke-width="2"/>
    <path d="M8 1v6M24 1v6" stroke="#3a2306" stroke-width="2"/>
    <g fill="#3a2306"><rect x="7" y="13" width="4" height="3.5"/><rect x="14" y="13" width="4" height="3.5"/><rect x="21" y="13" width="4" height="3.5"/><rect x="7" y="20" width="4" height="3.5"/><rect x="14" y="20" width="4" height="3.5"/><rect x="21" y="20" width="4" height="3.5"/></g>
  </svg>
</div>

<footer class="abs footer">© Copyrights 2014 All rights Reserved</footer>

</body>
</html>
```